SkyvornQ Business Cards and Stationary Design

Need a design for our business cards and stationary. I want to carry on the theme of the logo. I want the business cards to have a design on the back. I would like the business cards and the stationary to carry the same theme, design scheme, and branding

Target Market(s)

Airlines and Maintenance Facilities

Industry/Entity Type

Aviation

Contact Information for Business Card

Name
Position Title
Address: 4827 Trellis Hollow Road, Fort Pierce, Florida, 34951
Office Number
Mobile Number
Email
Website

Font styles to use
Serif
Sans Serif

Colors

Designer to choose colors to be used in the design.

```html
<!DOCTYPE html>
<html lang="en">
<head>
<meta charset="utf-8">
<title>SkyvornQ Business Card</title>
<link href="https://fonts.googleapis.com/css2?family=Montserrat:wght@700&family=Fira+Sans+Condensed:wght@400;600&family=Open+Sans:wght@400&display=swap" rel="stylesheet">
<style>
  :root {
    --navy: #14284d;
    --navy-deep: #1f3567;
    --sky: #29a3dc;
    --mid-blue: #2272ad;
    --white: #ffffff;
    --backdrop: #5e5e60;
    --ink: #2a2a2a;
  }
  * { margin: 0; padding: 0; box-sizing: border-box; }
  html, body { width: 1200px; height: 1073px; overflow: hidden; }
  body { background: var(--backdrop); position: relative; font-family: "Open Sans", sans-serif; }

  .card {
    position: absolute;
    width: 826px; height: 472px;
    border-radius: 40px;
    overflow: hidden;
    border: 1px solid #222;
  }
  .card-front { left: 57px; top: 53px; background: var(--navy); }
  .card-back { left: 311px; top: 551px; background: var(--white); }
  .card-art { position: absolute; inset: 0; width: 100%; height: 100%; }

  .brand-name {
    position: absolute;
    font-family: "Montserrat", sans-serif;
    font-weight: 700;
    color: var(--navy);
    letter-spacing: 0.16em;
    white-space: nowrap;
  }
  .card-front .brand-mark {
    position: absolute; left: 160px; top: 85px;
    width: 126px; height: 126px; border-radius: 50%;
    border: 8px solid var(--mid-blue);
  }
  .card-front .brand-name { left: 28px; top: 233px; font-size: 42px; }

  .holder { position: absolute; right: 34px; top: 82px; text-align: right; color: var(--white); font-family: "Fira Sans Condensed", sans-serif; }
  .holder-name { font-weight: 600; font-size: 24px; letter-spacing: 0.01em; line-height: 30px; }
  .holder-title { font-weight: 400; font-size: 21px; line-height: 28px; }

  .contact { position: absolute; right: 34px; top: 233px; list-style: none; color: var(--white); font-size: 18.5px; text-align: right; }
  .contact li { display: flex; align-items: center; justify-content: flex-end; gap: 6px; height: 33.5px; }
  .contact .icon { width: 18px; height: 18px; flex: none; }
  .contact .address { margin-top: 24px; align-items: flex-start; height: auto; line-height: 29px; }
  .contact .address .icon { margin-top: 6px; }

  .card-back .brand-mark {
    position: absolute; left: 64px; top: 54px;
    width: 342px; height: 342px; border-radius: 50%;
    border: 20px solid var(--mid-blue);
  }
  .card-back .brand-name { left: 446px; top: 186px; font-size: 41px; }
  .card-back .site { position: absolute; left: 491px; top: 252px; font-size: 19px; letter-spacing: 0.2em; color: var(--ink); }
</style>
</head>
<body>

<section class="card card-front">
  <svg class="card-art" viewBox="0 0 893 510" preserveAspectRatio="none" aria-hidden="true">
    <defs>
      <linearGradient id="swoosh" x1="0" y1="1" x2="1" y2="0">
        <stop offset="0" stop-color="#1f3567"/>
        <stop offset="0.55" stop-color="#29a3dc"/>
        <stop offset="1" stop-color="#2466a0"/>
      </linearGradient>
      <linearGradient id="corner-band" x1="0" y1="1" x2="1" y2="0">
        <stop offset="0" stop-color="#1f3567"/>
        <stop offset="0.6" stop-color="#29a3dc"/>
        <stop offset="1" stop-color="#1f3567"/>
      </linearGradient>
    </defs>
    <path fill="url(#swoosh)" d="M598 0 L658 0 C630 220 440 490 130 483 C80 482 30 470 0 458 L0 445 C30 460 80 475 130 475 C430 470 590 200 598 0 Z"/>
    <path fill="url(#corner-band)" d="M0 160 C60 90 140 30 190 0 L205 0 C130 50 60 120 0 212 Z"/>
    <path fill="#ffffff" d="M0 212 C60 120 130 50 205 0 L598 0 C590 200 430 470 130 475 C80 475 30 460 0 445 Z"/>
  </svg>

  <span class="brand-mark" aria-hidden="true"></span>
  <span class="brand-name">SKYVORNQ</span>

  <div class="holder">
    <p class="holder-name">DORIAN FELLWEATHER</p>
    <p class="holder-title">PRESIDENT</p>
  </div>

  <ul class="contact">
    <li>
      <svg class="icon" viewBox="0 0 20 20" aria-hidden="true"><circle cx="10" cy="10" r="8.8" fill="none" stroke="#fff" stroke-width="1.5"/><path d="M6.5 5.5 L8.3 5.3 L9 7.8 L8 8.6 C8.6 10 9.8 11.3 11.3 12 L12.2 11 L14.6 11.8 L14.4 13.5 C10 14 6 10 6.5 5.5Z" fill="#fff"/></svg>
      <span>012-345-6789</span>
    </li>
    <li>
      <svg class="icon" viewBox="0 0 20 20" aria-hidden="true"><circle cx="10" cy="10" r="8.8" fill="none" stroke="#fff" stroke-width="1.5"/><rect x="7" y="5" width="6" height="10" rx="1.2" fill="none" stroke="#fff" stroke-width="1.4"/></svg>
      <span>012-345-6789</span>
    </li>
    <li>
      <svg class="icon" viewBox="0 0 20 20" aria-hidden="true"><circle cx="10" cy="10" r="8.8" fill="none" stroke="#fff" stroke-width="1.5"/><rect x="5.5" y="7" width="9" height="6.5" fill="none" stroke="#fff" stroke-width="1.3"/><path d="M5.5 7 L10 10.5 L14.5 7" fill="none" stroke="#fff" stroke-width="1.3"/></svg>
      <span>info@skyvornq.com</span>
    </li>
    <li>
      <svg class="icon" viewBox="0 0 20 20" aria-hidden="true"><g fill="none" stroke="#fff" stroke-width="1.2"><circle cx="10" cy="10" r="8.5"/><ellipse cx="10" cy="10" rx="3.8" ry="8.5"/><path d="M1.5 10 H18.5 M3 5.5 H17 M3 14.5 H17"/></g></svg>
      <span>www.skyvornq.com</span>
    </li>
    <li class="address">
      <svg class="icon" viewBox="0 0 20 20" aria-hidden="true"><circle cx="10" cy="10" r="8.8" fill="none" stroke="#fff" stroke-width="1.5"/><path d="M10 15 C7 11.5 6.5 10 6.5 8.5 A3.5 3.5 0 0 1 13.5 8.5 C13.5 10 13 11.5 10 15Z" fill="none" stroke="#fff" stroke-width="1.3"/><circle cx="10" cy="8.5" r="1.3" fill="#fff"/></svg>
      <span>4827 Trellis Hollow Road, Fort Pierce<br>Florida, 34951</span>
    </li>
  </ul>
</section>

<section class="card card-back">
  <span class="brand-mark" aria-hidden="true"></span>
  <span class="brand-name">SKYVORNQ</span>
  <p class="site">www.skyvornq.com</p>
</section>

</body>
</html>
```